Business Book - Building Calm Mornings at the Office (Hand Off the Small Stuff and Keep the Spark)

I'm looking for a cover that appeals to successful business people who are used to reading business titles.

The cover should feel familiar and fit in with the existing canon of bestselling business books with a vibrant, but professional look (see attached).

I want my book to stand out, but not to be frivolous. Abstract is probably best. Or close to it.

Please feel free to use my brand colours, or go with something else -

Teal
HEX #199BAB
25 / 155 / 171

Coral
HEX #EE786E
238 / 120/ 110

I don't want to include anything connected with robots or gendered assistants/business people. Or headsets.

It's only 24 hours which is mental

```html
<!DOCTYPE html>
<html lang="en">
<head>
<meta charset="utf-8">
<title>Building Calm Mornings at the Office – Book Cover</title>
<link rel="stylesheet" href="https://fonts.googleapis.com/css2?family=Saira+Extra+Condensed:wght@600&family=Montserrat:wght@500;700&display=swap">
<style>
  :root {
    --backdrop: #8e8f92;
    --paper: #ffffff;
    --ink: #0d0d14;
    --coral: #ee786e;
  }
  html, body {
    margin: 0;
    padding: 0;
    width: 1200px;
    height: 1077px;
    overflow: hidden;
    background: var(--backdrop);
  }
  .book-cover {
    position: absolute;
    left: 262px;
    top: 32px;
    width: 674px;
    height: 1012px;
    background: var(--paper);
  }
  .book-cover svg { display: block; }
  .title-lead {
    font-family: "Saira Extra Condensed", "Arial Narrow", sans-serif;
    font-weight: 600;
    fill: var(--ink);
  }
  .title-main {
    font-family: "Saira Extra Condensed", "Arial Narrow", sans-serif;
    font-weight: 600;
    fill: var(--coral);
  }
  .subtitle {
    font-family: "Montserrat", Arial, sans-serif;
    font-weight: 500;
    fill: var(--ink);
    letter-spacing: 1px;
  }
  .author-band { fill: var(--coral); }
  .author-name {
    font-family: "Montserrat", Arial, sans-serif;
    font-weight: 700;
    fill: var(--paper);
    letter-spacing: 2px;
  }
</style>
</head>
<body>
  <div class="book-cover">
    <svg width="674" height="1012" viewBox="0 0 674 1012" xmlns="http://www.w3.org/2000/svg">
      <defs>
        <linearGradient id="photo-tones" x1="0" y1="0" x2="1" y2="1">
          <stop offset="0" stop-color="#e9ecf2"/>
          <stop offset="0.35" stop-color="#9aa3b8"/>
          <stop offset="0.6" stop-color="#2a3048"/>
          <stop offset="1" stop-color="#c7cdd8"/>
        </linearGradient>
        <linearGradient id="photo-fade" x1="0" y1="0" x2="0" y2="1">
          <stop offset="0.7" stop-color="#ffffff" stop-opacity="0"/>
          <stop offset="1" stop-color="#ffffff" stop-opacity="1"/>
        </linearGradient>
      </defs>

      <g class="cover-photo" role="img" aria-label="Photo of a business person at a desk gesturing over a glowing world map of connected network icons">
        <rect x="0" y="0" width="674" height="500" fill="url(#photo-tones)"/>
        <rect x="0" y="0" width="674" height="500" fill="url(#photo-fade)"/>
      </g>

      <text class="title-lead" x="61" y="527" font-size="84" textLength="520" lengthAdjust="spacingAndGlyphs">BUILDING CALM MORNINGS</text>
      <text class="title-main" x="63" y="708" font-size="246" textLength="550" lengthAdjust="spacingAndGlyphs">AT THE</text>
      <text class="title-main" x="86" y="848" font-size="176" textLength="527" lengthAdjust="spacingAndGlyphs">OFFICE</text>

      <text class="subtitle" x="337" y="896" font-size="27" text-anchor="middle">HAND OFF THE SMALL STUFF</text>
      <text class="subtitle" x="337" y="929" font-size="27" text-anchor="middle">AND KEEP THE SPARK</text>

      <rect class="author-band" x="0" y="953" width="674" height="59"/>
      <text class="author-name" x="337" y="998" font-size="43" text-anchor="middle">AUTHOR NAME</text>
    </svg>
  </div>
</body>
</html>
```